BOLD & MINIMALIST DESIGN NEEDED

We want a very bold but minimalistic business card design that is impactful and utilizes both sides of the business card. Our current logo is included for your use.

We want bold fonts and good use of negative space. We don't want the logo to overpower the design.

Target Market(s)

Professionals who are building new commercial buildings.

Industry/Entity Type

Construction

Contact Information for Business Card

Name, Title, email, office phone, cell phone, website

Font styles to use
Serif
Sans Serif

Requirements
Must have
• Bold design!

```html
<!DOCTYPE html>
<html lang="en">
<head>
<meta charset="utf-8">
<title>Ridgeline Design + Build — Business Card</title>
<link rel="stylesheet" href="https://fonts.googleapis.com/css2?family=Montserrat:wght@400;500;800;900&display=swap">
<style>
  :root {
    --stage: #2a2a2a;
    --card-white: #ffffff;
    --card-black: #1c1c1c;
    --pattern-dark: #262626;
    --ink: #111111;
    --green: #6cc22a;
    --muted: #222222;
  }
  * { box-sizing: border-box; margin: 0; padding: 0; }
  html, body { width: 1200px; height: 900px; overflow: hidden; }
  body {
    background: var(--stage);
    font-family: "Montserrat", Arial, sans-serif;
    color: var(--ink);
    position: relative;
  }
  .card {
    position: absolute;
    left: 260px;
    width: 680px;
    height: 388px;
    box-shadow: 0 14px 36px rgba(0,0,0,.5);
  }
  .card--front { top: 42px; background: var(--card-white); }
  .card--back { top: 470px; background: var(--card-black); overflow: hidden; }

  /* front */
  .brand {
    position: absolute;
    left: 44px;
    top: 150px;
    width: 240px;
    display: flex;
    align-items: center;
    gap: 10px;
  }
  .brand__mark {
    width: 18px; height: 18px; border-radius: 50%;
    background: var(--green); flex: none;
  }
  .brand__name {
    font-weight: 900;
    font-size: 24px;
    line-height: 1.05;
    letter-spacing: .5px;
    text-transform: uppercase;
    color: var(--ink);
  }
  .divider {
    position: absolute;
    left: 320px; top: 72px;
    width: 2px; height: 244px;
    background: var(--green);
  }
  .contact {
    position: absolute;
    left: 350px; top: 74px;
    width: 310px;
  }
  .contact__name {
    font-weight: 800;
    font-size: 26px;
    color: var(--green);
    text-transform: uppercase;
    letter-spacing: 1px;
    line-height: 1;
  }
  .contact__title {
    font-size: 13px;
    letter-spacing: 1.5px;
    text-transform: uppercase;
    margin-top: 6px;
    color: var(--muted);
  }
  .contact__address {
    font-size: 13px;
    line-height: 1.4;
    margin-top: 22px;
    font-style: normal;
    color: var(--muted);
  }
  .contact__list {
    list-style: none;
    margin-top: 22px;
    font-size: 13px;
    line-height: 1.55;
    color: var(--muted);
  }
  .contact__list li { display: flex; align-items: center; gap: 8px; }
  .contact__list svg { width: 13px; height: 13px; flex: none; }
  .accent { color: var(--green); }

  /* back */
  .back-pattern {
    position: absolute; inset: 0;
    background: linear-gradient(135deg, var(--pattern-dark), var(--card-black) 60%);
  }
  .back-brand {
    position: absolute;
    right: 36px; bottom: 30px;
    font-weight: 900;
    font-size: 15px;
    letter-spacing: .5px;
    text-transform: uppercase;
    color: var(--green);
  }
</style>
</head>
<body>

<section class="card card--front" aria-label="Business card front">
  <div class="brand">
    <span class="brand__mark"></span>
    <span class="brand__name">Ridgeline<br>Design + Build</span>
  </div>

  <div class="divider"></div>

  <div class="contact">
    <p class="contact__name">Mark Ellison</p>
    <p class="contact__title">Owner</p>
    <address class="contact__address">480 Timberline Road,<br>Suite #210</address>
    <ul class="contact__list">
      <li>
        <svg viewBox="0 0 24 24" fill="var(--green)"><path d="M6.6 10.8a15 15 0 0 0 6.6 6.6l2.2-2.2a1 1 0 0 1 1-.25 11.4 11.4 0 0 0 3.6.57 1 1 0 0 1 1 1V20a1 1 0 0 1-1 1A17 17 0 0 1 3 4a1 1 0 0 1 1-1h3.5a1 1 0 0 1 1 1c0 1.25.2 2.45.57 3.57a1 1 0 0 1-.25 1z"/></svg>
        (555) 014-2286
      </li>
      <li>
        <svg viewBox="0 0 24 24" fill="none" stroke="var(--green)" stroke-width="2"><rect x="3" y="10" width="18" height="11" rx="2"/><path d="M2 8c3-4 17-4 20 0"/><circle cx="12" cy="15.5" r="2.5"/></svg>
        (555) 014-2286
      </li>
      <li>
        <svg viewBox="0 0 24 24" fill="none" stroke="var(--green)" stroke-width="2"><rect x="3" y="5" width="18" height="14"/><path d="M3 5l9 8 9-8"/></svg>
        ridgelinebuild@example.com
      </li>
      <li>
        <svg viewBox="0 0 24 24" fill="none" stroke="var(--green)" stroke-width="2"><circle cx="12" cy="12" r="9"/><path d="M3 12h18M12 3c3 3 3 15 0 18M12 3c-3 3-3 15 0 18"/></svg>
        <span>www.<span class="accent">ridgelinebuild</span>.com</span>
      </li>
    </ul>
  </div>
</section>

<section class="card card--back" aria-label="Business card back">
  <div class="back-pattern" role="img" aria-label="Tone-on-tone repeating brand pattern on black"></div>
  <span class="back-brand">Ridgeline</span>
</section>

</body>
</html>
```